I have a logo and need to design the business card and stationery.
Updates

The uploaded logo image named as GREYMARSH CONSTRUCTION which is to be replaced to GREYMARSH CONTRACTS. Kindly add below details and submit the designs- Company name- Greymarsh Engineering Contracts LLP Name & Post- Kelvan Joshi (Designated Partner) Address- Block No.317, Wing C, Tulvo Trade Court, Manek Pural Road, Ruparel Industrial Estate, Goregaon(E), Mumbai - 400 063 Contact- +91 97415 60382 Email- kelvanjoshi@mailbrook.example Website- www.greymarshcontracts.example Contact for Letterhead- +91-22-28754193

Hi Tovin Rahul, We are liking your Design #28860835. We have suggested some changes which are mentioned in feedback. Kindly revert with it asap to finalize this design.

Colors

Designer to choose colors to be used in the design.

```html
<!DOCTYPE html>
<html lang="en">
<head>
<meta charset="utf-8">
<title>Greymarsh Contracts – Stationery</title>
<link href="https://fonts.googleapis.com/css2?family=Figtree:wght@400;700;800&display=swap" rel="stylesheet">
<style>
:root{
  --backdrop:#c2cfce;
  --ink:#232d31;
  --ink-soft:#353f43;
  --sage:#8a9b98;
  --shadow:#6b7e7b;
  --flap-edge:#dde6e3;
  --paper:#ffffff;
  --text:#2b3336;
}
*{margin:0;padding:0;box-sizing:border-box}
html,body{width:1200px;height:857px;overflow:hidden;background:var(--backdrop);font-family:'Figtree',sans-serif;color:var(--text)}
.canvas{position:relative;width:1200px;height:857px}
.abs{position:absolute}
.drop{position:absolute;background:var(--shadow);border-radius:0 0 50% 50%/0 0 100% 100%}

/* wordmark */
.wordmark{position:absolute;text-align:center;font-family:'Figtree',sans-serif;font-weight:800;line-height:1}
.wordmark .name{display:block;letter-spacing:.02em}
.wordmark .sub{display:block;letter-spacing:1.05em;margin-right:-1.05em}

/* envelope back */
.env-back{left:59px;top:69px;width:527px;height:348px;background:var(--paper)}
.env-back .flap-edge{position:absolute;left:0;top:0;width:100%;height:126px;background:var(--flap-edge);border-radius:0 0 28px 28px}
.env-back .flap{position:absolute;left:0;top:0;width:100%;height:113px;background:var(--ink);border-radius:0 0 28px 28px}

/* envelope front */
.env-front{left:62px;top:440px;width:527px;height:347px;background:var(--paper)}
.stamp-area{position:absolute;left:411px;top:34px;width:66px;height:43px;background:var(--ink)}
.recipient{position:absolute;right:50px;top:116px;text-align:right;color:var(--sage);font-size:8.6px;line-height:12px}
.recipient .label{margin-bottom:12px}
.env-front .rule-line{position:absolute;left:19px;top:303px;width:483px;height:1px;background:#c9d2d0}
.foot{position:absolute;left:0;width:100%;text-align:center;color:var(--sage)}
.foot b{font-weight:700}

/* letterhead */
.letterhead{left:699px;top:71px;width:383px;height:541px;background:var(--paper);border:1px solid #7d8d8a}
.letterhead .head{position:absolute;left:0;top:0;width:100%;height:64px;background:var(--ink)}
.letterhead h1{position:absolute;left:0;width:100%;top:90px;text-align:center;font-size:12.5px;font-weight:800;color:var(--ink)}
.letterhead h2{position:absolute;left:0;width:100%;text-align:center;font-size:9px;font-weight:800;color:var(--ink)}
.letterhead p{position:absolute;left:37px;width:310px;font-size:6.9px;line-height:9.6px;color:var(--text)}
.letterhead .rule-line{position:absolute;left:37px;top:504px;width:310px;height:1px;background:#c9d2d0}

/* business card */
.card-front{left:621px;top:642px;width:254px;height:145px;background:var(--paper);border:1px solid #7d8d8a}
.card-front .band{position:absolute;left:0;bottom:0;width:100%;height:38px;background:var(--ink);color:#b6c3c1;text-align:center;font-size:6.4px;line-height:8.4px;padding-top:7px}
.person{position:absolute;left:23px;top:76px}
.person .who{font-size:10.5px;font-weight:800;color:var(--ink)}
.person .role{font-size:5.5px;letter-spacing:.03em;color:var(--text);margin-top:2px}
.contacts{position:absolute;left:121px;top:69px;font-size:6.8px;line-height:9.3px;color:var(--ink)}
.contacts div{display:flex;align-items:center;gap:3px}
.contacts svg{width:8px;height:8px;flex:none}
.card-back{left:892px;top:644px;width:254px;height:145px;background:var(--ink)}
</style>
</head>
<body>
<div class="canvas">

  <!-- envelope back -->
  <div class="drop" style="left:70px;top:416px;width:505px;height:9px"></div>
  <section class="abs env-back">
    <div class="flap-edge"></div>
    <div class="flap">
      <div class="wordmark" style="left:0;width:100%;top:59px;color:var(--ink-soft)">
        <span class="name" style="font-size:22px">GREYMARSH</span>
        <span class="sub" style="font-size:6px;margin-top:4px">CONTRACTS</span>
      </div>
    </div>
  </section>

  <!-- envelope front -->
  <div class="drop" style="left:73px;top:786px;width:505px;height:10px"></div>
  <section class="abs env-front">
    <div class="stamp-area" role="img" aria-label="Postage stamp"></div>
    <div class="recipient">
      <div class="label">Name and address of the recipient</div>
      Block No.317, Wing C, Tulvo Trade Court,<br>
      Manek Pural Road, Ruparel Industrial Estate,<br>
      Goregaon(E), Mumbai - 400 063
    </div>
    <div class="wordmark" style="left:0;width:100%;top:267px;color:var(--sage)">
      <span class="name" style="font-size:16.5px">GREYMARSH</span>
      <span class="sub" style="font-size:5px;margin-top:4px">CONTRACTS</span>
    </div>
    <div class="rule-line"></div>
    <div class="foot" style="top:311px;font-size:6.3px"><b>Address:</b> Block No.317, Wing C, Tulvo Trade Court, Manek Pural Road, Ruparel Industrial Estate, Goregaon(E), Mumbai - 400 063 &nbsp;/&nbsp; <b>Phone:</b> +91-22-28754193</div>
    <div class="foot" style="top:323px;font-size:6.5px;font-weight:700">WWW.GREYMARSHCONTRACTS.EXAMPLE</div>
  </section>

  <!-- letterhead -->
  <div class="drop" style="left:711px;top:611px;width:359px;height:10px"></div>
  <section class="abs letterhead">
    <div class="head">
      <div class="wordmark" style="left:0;width:100%;top:33px;color:var(--ink-soft)">
        <span class="name" style="font-size:13px">GREYMARSH</span>
        <span class="sub" style="font-size:3.6px;margin-top:3px">CONTRACTS</span>
      </div>
    </div>
    <h1>LOREM IPSUM DOLOR SIT AMET</h1>
    <p style="top:117px">consectetuer adipiscing elit, sed diam nonummy nibh euismod tincidunt ut laoreet doloe magna aliquam erat volutpat. Ut wisi enim ad minim veniam, quis nostrud exerci tation ullamcorper suscipit lobortis nisl ut aliquip ex ea commodo consequat. Duis autem vel eum iriure dolor in hendrerit in vulputate velit esse molestie consequat, vel illum dolore eu feugiat nulla facilisis at vero eros et accumsan et iusto odio dignissim qui blandit praesent luptatum zzril delenit augue duis dolore te feugait nulla facilisi.</p>
    <h2 style="top:196px">Lorem ipsum dolor sit amet, cons ectetuer adipiscing elit</h2>
    <p style="top:217px">Lorem ipsum dolor sit amet, cons ectetuer adipiscing elit, sed diam nonummy nibh euismod tincidunt ut laoreet dolore magna aliquam erat volutpat. Ut wisi enim ad minim veniam, quis nostrud exerci tation ullamcorper suscipit lobortis nisl ut aliquip ex ea commodo consequat. Lorem ipsum dolor sit amet, consectetuer adipiscing elit, sed diam nonummy nibh euismod tincidunt ut laoreet dolore magna aliquam erat volutpat. Ut wisi enim ad minim veniam, quis nostrud exerci tation ullamcorper suscipit lobortis nisl ut aliquip ex ea commodo consequat.</p>
    <p style="top:284px">Duis autem vel eum iriure dolor in hendrerit in vulputate velit esse molestie consequat, vel illum dolore eu feugiat nulla facilisis at vero eros et accumsan et iusto odio dignissim qui blandit praesent luptatum zzril delenit augue duis dolore te feugait nulla facilisi.</p>
    <p style="top:322px">Lorem ipsum dolor sit amet, cons ectetuer adipiscing elit, sed diam nonummy nibh euismod tincidunt ut laoreet dolore magna aliquam erat volutpat. Ut wisi enim ad minim veniam, quis nostrud exerci tation ullamcorper suscipit lobortis nisl ut aliquip ex ea commodo consequat. Lorem ipsum dolor sit amet, consectetuer adipiscing elit, sed diam nonummy nibh euismod tincidunt ut laoreet dolore magna aliquam erat volutpat. Ut wisi enim ad minim veniam, quis nostrud exerci tation ullamcorper suscipit lobortis nisl ut aliquip ex ea commodo consequat.</p>
    <p style="top:390px">Duis autem vel eum iriure dolor in hendrerit in vulputate velit esse molestie consequat, vel illum dolore eu feugiat nulla facilisis at vero eros et accumsan et iusto odio dignissim qui blandit praesent luptatum zzril delenit augue duis dolore te feugait nulla facilisi.</p>
    <h2 style="top:440px">Lorem ipsum dolor sit amet</h2>
    <p style="top:460px">Lorem ipsum dolor sit amet, cons ectetuer adipiscing elit, sed diam nonummy nibh euismod tincidunt ut laoreet dolore magna aliquam erat volutpat. Ut wisi enim ad minim veniam, quis nostrud exerci tation ullamcorper suscipit lobortis nisl ut aliquip ex ea commodo consequat.</p>
    <div class="rule-line"></div>
    <div class="foot" style="top:511px;font-size:3.9px;color:var(--sage)"><b>Address:</b> Block No.317, Wing C, Tulvo Trade Court, Manek Pural Road, Ruparel Industrial Estate, Goregaon(E), Mumbai - 400 063 &nbsp;/&nbsp; <b>Phone:</b> +91-22-28754193</div>
    <div class="foot" style="top:519px;font-size:5.2px;font-weight:700">WWW.GREYMARSHCONTRACTS.EXAMPLE</div>
  </section>

  <!-- business card front -->
  <div class="drop" style="left:625px;top:786px;width:245px;height:8px"></div>
  <section class="abs card-front">
    <div class="wordmark" style="left:0;width:100%;top:33px;color:var(--ink)">
      <span class="name" style="font-size:13.5px">GREYMARSH</span>
      <span class="sub" style="font-size:4px;margin-top:3px">CONTRACTS</span>
    </div>
    <div class="person">
      <div class="who">Kelvan Joshi</div>
      <div class="role">DESIGNATED PARTNER</div>
    </div>
    <div class="contacts">
      <div><svg viewBox="0 0 10 10" fill="none" stroke="#232d31" stroke-width=".8"><path d="M2 1l2 2-1 1.2a6 6 0 0 0 2.8 2.8L7 6l2 2-1.3 1.3C4.5 9 1 5.5.7 2.3z"/></svg>+91 97415 60382</div>
      <div><svg viewBox="0 0 10 10" fill="none" stroke="#232d31" stroke-width=".8"><rect x=".8" y="2" width="8.4" height="6"/><path d="M.8 2L5 5.5 9.2 2"/></svg>kelvanjoshi@mailbrook.example</div>
      <div><svg viewBox="0 0 10 10" fill="none" stroke="#232d31" stroke-width=".8"><circle cx="5" cy="5" r="4.2"/><ellipse cx="5" cy="5" rx="1.8" ry="4.2"/><path d="M.8 5h8.4M1.5 3h7M1.5 7h7"/></svg>www.greymarshcontracts.example</div>
    </div>
    <div class="band">Block No.317, Wing C, Tulvo Trade Court, Manek Pural Road,<br>Ruparel Industrial Estate, Goregaon(E), Mumbai - 400 063</div>
  </section>

  <!-- business card back -->
  <div class="drop" style="left:896px;top:788px;width:245px;height:8px"></div>
  <section class="abs card-back">
    <div class="wordmark" style="left:0;width:100%;top:66px;color:var(--ink-soft)">
      <span class="name" style="font-size:22px">GREYMARSH</span>
      <span class="sub" style="font-size:6px;margin-top:4px">CONTRACTS</span>
    </div>
  </section>

</div>
</body>
</html>
```